The best Social Research house in LatinAmerica needs a Business Card

We need a greeting card that does justice to our everyday work. Marenta Civica is a group of highly selected social academic minds (6 academicians selected among 800+ candidates) that analyses the field work done by our network of 56 social anthropologists in 7 Latin American countries. We spend months studying different social phenomena or groups of people and then translate the findings into powerful insights and strategic marketing actions for our clients (from Banks to TV networks, from top worldwide consumer product Companies to Government policy design or even new product innovation initiatives). We translate social academic knowledge into tangible actions. We already have a logo and we like it, but remain open for new and different proposals on size or form. We do something very different and we need a card as different as we are.
Target Market(s)
Top Management from Top Companies that need (and like) to be surprised!
Industry/Entity Type
Marketing
Look and feel

```html
<!DOCTYPE html>
<html lang="es">
<head>
<meta charset="utf-8">
<title>Marenta Civica — Tarjeta de presentación</title>
<link rel="stylesheet" href="https://fonts.googleapis.com/css2?family=Arvo:wght@400;700&display=swap">
<style>
  :root {
    --page: #ecebe8;
    --card-green: #5aae30;
    --card-green-deep: #4f9f28;
    --card-white: #fbfbfb;
    --teal: #0f8d76;
    --leaf: #5aae30;
    --ink: #2e2e2e;
    --ghost: #e6e6e6;
    --ghost-green: rgba(255,255,255,0.10);
  }
  * { box-sizing: border-box; margin: 0; padding: 0; }
  html, body {
    width: 1200px; height: 900px; overflow: hidden;
    background: var(--page);
    font-family: "Arvo", Georgia, serif;
  }
  .stage {
    position: relative; width: 1200px; height: 900px;
  }
  .card {
    position: absolute; left: 320px; width: 560px; height: 320px;
    overflow: hidden;
    box-shadow: 0 6px 18px rgba(0,0,0,0.18);
  }
  .card--front { top: 70px; background: linear-gradient(135deg, var(--card-green) 0%, var(--card-green-deep) 100%); }
  .card--back { top: 470px; background: var(--card-white); }

  .ghost-mark {
    position: absolute; border-radius: 50%;
  }
  .card--front .ghost-mark { width: 340px; height: 340px; right: -110px; top: -120px; background: var(--ghost-green); }
  .card--back .ghost-mark { width: 300px; height: 300px; right: -90px; top: 20px; background: var(--ghost); }

  .brand {
    position: absolute; display: flex; align-items: center; gap: 12px;
    font-weight: 700; white-space: nowrap;
  }
  .brand__dot { width: 30px; height: 30px; border-radius: 50%; flex: none; }
  .card--front .brand { left: 40px; bottom: 48px; font-size: 34px; color: #ffffff; }
  .card--front .brand__dot { background: #ffffff; }
  .card--back .brand { left: 32px; top: 30px; font-size: 30px; color: var(--teal); }
  .card--back .brand__dot { background: var(--teal); }

  .contact {
    position: absolute; left: 40px; top: 128px;
    padding-left: 16px; border-left: 2px solid var(--teal);
    color: var(--ink);
  }
  .contact__name { font-size: 24px; font-weight: 400; line-height: 1.1; }
  .contact__role { font-size: 15px; margin-top: 4px; }
  .contact__lines { margin-top: 20px; font-size: 13px; line-height: 1.55; }
  .contact__label { color: var(--teal); font-style: italic; display: inline-block; width: 16px; }
  .contact__address { font-size: 13px; margin-top: 2px; }
</style>
</head>
<body>
  <main class="stage">
    <section class="card card--front" aria-label="Frente de la tarjeta">
      <span class="ghost-mark" aria-hidden="true"></span>
      <div class="brand"><span class="brand__dot" aria-hidden="true"></span>Marenta Civica</div>
    </section>

    <section class="card card--back" aria-label="Reverso de la tarjeta">
      <span class="ghost-mark" aria-hidden="true"></span>
      <div class="brand"><span class="brand__dot" aria-hidden="true"></span>Marenta Civica</div>
      <div class="contact">
        <p class="contact__name">Tomas Arriaga</p>
        <p class="contact__role">Gabinete de Análisis</p>
        <div class="contact__lines">
          <p><span class="contact__label">t</span>(55) 5550 1274</p>
          <p><span class="contact__label">e</span>tomas.arriaga@marenta-civica.com</p>
          <p class="contact__address">Calle Olmos 14. Col. Roma, Mexico DF 06700. MX.</p>
        </div>
      </div>
    </section>
  </main>
</body>
</html>
```